Business Cards for new orthopaedic surgery practice

My husband and I are starting our own orthopaedic surgery practice. We are looking for a business card that is uniform, but one will have my name/title and the other will have his. You can just create one design with my name on it for now. But when I choose your design as the winning design I will ask that you add another copy with his name/title.

We are looking for classy, simple, elite all in one. We like dark blues/a little gold/yellow. Something that goes with our logo. We want our logo incorporated. Here is all the info you need:
Business name: RV Bone & Vitality Center
Location: 38517 North Willowmere Ave
Coral Springs, FL 33071
Phone: 954-218-4063
Fax: 954-582-7341
Email: info@myrvbonecare.example

Names: Lydia Vance, M.D.
Board Certified Hand and Upper Extremity Surgeon

Ebo Dansu, M.D.
Board Certified Hip & Knee Replacement/General Orthopaedic Surgeon

Can decide what you want to put on the back. Maybe a slogan:
Steady Hands. Lasting Strength

I am just going to upload our logo. The only thing is if we select you as the winning design, the location, and phone numbers may change. We will need your help to update that once fully solidified.

Industry/Entity Type

Medical

Contact Information for Business Card

Colors
0054AA
0677BA
7BADD7
CADEEF
E8F1F8
0094D4
00A9DD
6FCCEA
C7EBF8
E9F6FB

Requirements
Must have
• class, appeal,
Should not have
• We want to air on the side of masculine if we are looking at masculine vs. feminine feel. But we still want it classy, sophisticated, and something we will love

```html
<!DOCTYPE html>
<html lang="en">
<head>
<meta charset="utf-8">
<title>RV Bone &amp; Vitality Center – Business Card</title>
<link rel="stylesheet" href="https://fonts.googleapis.com/css2?family=Cinzel:wght@600;700&family=Roboto:wght@400&display=swap">
<style>
  :root {
    --page-bg: #e2e2e0;
    --navy: #1c3d8f;
    --back-navy: #2b4a8e;
    --cyan: #1ba8d5;
    --paper: #f4f4f2;
    --ink: #3b3b3b;
    --white: #ffffff;
  }
  * { box-sizing: border-box; margin: 0; padding: 0; }
  html, body {
    width: 1200px; height: 884px; overflow: hidden;
    background: var(--page-bg);
  }
  .sheet {
    width: 1200px; height: 884px;
    display: flex; flex-direction: column;
    align-items: center; justify-content: center; gap: 44px;
  }
  .card {
    position: relative;
    width: 640px; height: 360px;
    overflow: hidden;
  }

  /* Front */
  .card-front { background: var(--paper); }
  .top-band {
    position: absolute; left: 0; top: 0; right: 0; height: 13px;
    background: var(--navy);
  }
  .identity { position: absolute; left: 47px; top: 62px; }
  .person-name {
    font-family: 'Cinzel', serif; font-weight: 700;
    font-size: 21px; color: var(--navy); letter-spacing: 0.2px;
    line-height: 1.1;
  }
  .person-title {
    font-family: 'Roboto', sans-serif; font-size: 17px;
    color: var(--cyan); line-height: 1.3; margin-top: 3px;
  }
  .brand-name {
    position: absolute; left: 340px; width: 250px; top: 92px;
    text-align: center;
    font-family: 'Cinzel', serif; font-weight: 700;
    font-size: 20px; line-height: 1.3; color: var(--navy);
  }
  .contact-list {
    position: absolute; left: 47px; top: 172px;
    list-style: none;
    font-family: 'Roboto', sans-serif; font-size: 18px; color: var(--ink);
  }
  .contact-list li {
    display: flex; align-items: center; gap: 7px; height: 24px;
  }
  .contact-icon { width: 17px; height: 17px; fill: var(--navy); flex: none; }
  .divider {
    position: absolute; left: 47px; right: 50px; top: 283px;
    height: 1px; background: var(--cyan);
  }
  .address {
    position: absolute; left: 47px; top: 296px;
    display: flex; align-items: center; gap: 7px;
    font-family: 'Roboto', sans-serif; font-size: 18px; color: var(--ink);
  }

  /* Back */
  .card-back {
    background: var(--back-navy);
    display: flex; flex-direction: column; align-items: center; justify-content: center;
  }
  .back-brand {
    font-family: 'Cinzel', serif; font-weight: 700;
    font-size: 36px; line-height: 1.25; color: var(--white);
    text-align: center;
  }
  .slogan {
    margin-top: 38px;
    font-family: 'Cinzel', serif; font-weight: 600;
    font-size: 14px; letter-spacing: 2.4px; color: var(--cyan);
    text-transform: uppercase;
  }
</style>
</head>
<body>
<main class="sheet">

  <section class="card card-front" aria-label="Business card front">
    <div class="top-band"></div>

    <div class="identity">
      <h1 class="person-name">LYDIA VANCE, M.D.</h1>
      <p class="person-title">Board Certified Hand and<br>Upper Extremity Surgeon</p>
    </div>

    <p class="brand-name">RV Bone &amp; Vitality<br>Center</p>

    <ul class="contact-list">
      <li>
        <svg class="contact-icon" viewBox="0 0 24 24" aria-hidden="true"><path d="M2 8c0-2 4-4 10-4s10 2 10 4v2h-5V8c-2-1-8-1-10 0v2H2z"/><path d="M6 12h12l2 8H4z"/></svg>
        954-218-4063
      </li>
      <li>
        <svg class="contact-icon" viewBox="0 0 24 24" aria-hidden="true"><path d="M7 3h10v5H7z"/><path d="M3 9h18v8h-3v-3H6v3H3z"/><path d="M7 15h10v6H7z"/></svg>
        954-582-7341
      </li>
      <li>
        <svg class="contact-icon" viewBox="0 0 24 24" aria-hidden="true"><path d="M2 5h20v14H2z M4 7v.5l8 6 8-6V7l-8 6z" fill-rule="evenodd"/></svg>
        info@myrvbonecare.example
      </li>
      <li>
        <svg class="contact-icon" viewBox="0 0 24 24" aria-hidden="true"><circle cx="12" cy="12" r="10"/><path d="M7 7c2 0 3 2 2 4s-3 1-3 4M15 5c-1 2 1 3 3 3M14 19c0-3 2-3 3-5" stroke="#f4f4f2" stroke-width="1.6" fill="none"/></svg>
        www.lvancehand.example
      </li>
    </ul>

    <div class="divider"></div>

    <p class="address">
      <svg class="contact-icon" viewBox="0 0 24 24" aria-hidden="true"><path d="M12 1a8 8 0 0 0-8 8c0 6 8 14 8 14s8-8 8-14a8 8 0 0 0-8-8zm0 11a3 3 0 1 1 0-6 3 3 0 0 1 0 6z"/></svg>
      38517 North Willowmere Ave, Coral Springs, FL 33071
    </p>
  </section>

  <section class="card card-back" aria-label="Business card back">
    <p class="back-brand">RV Bone &amp; Vitality<br>Center</p>
    <p class="slogan">Steady Hands. Lasting Strength</p>
  </section>

</main>
</body>
</html>
```